Residential & commercial landscaping company

Updated business cards for commercial and landscaping company. We would like to keep out logo, but just need a more updated business card.

```html
<!DOCTYPE html>
<html lang="en">
<head>
<meta charset="utf-8">
<title>GreenVale Business Cards</title>
<link rel="stylesheet" href="https://fonts.googleapis.com/css2?family=Oswald:wght@500;600&display=swap">
<style>
  :root {
    --backdrop: #a9a9a9;
    --green-light: #58c24b;
    --green-mid: #079a35;
    --green-dark: #066b34;
    --green-deep: #08772f;
    --white: #ffffff;
    --ink: #111111;
  }
  * { margin: 0; padding: 0; box-sizing: border-box; }
  html, body {
    width: 1200px; height: 1200px; overflow: hidden;
    background: radial-gradient(ellipse at center, #c4c4c4 0%, var(--backdrop) 55%, #7d7d7d 100%);
    font-family: "Oswald", sans-serif;
  }
  .canvas { position: relative; width: 1200px; height: 1200px; }
  .card {
    position: absolute; top: 303px; width: 370px; height: 594px;
    box-shadow: 3px 4px 6px rgba(0,0,0,0.35);
    overflow: hidden;
  }
  .card-front {
    left: 201px;
    background: linear-gradient(180deg, var(--green-light) 0%, #1fae3c 30%, var(--green-mid) 60%, var(--green-deep) 100%);
  }
  .front-brand {
    position: absolute; left: 0; right: 0; top: 488px;
    text-align: center; color: var(--white);
    font-weight: 600; font-size: 50px; letter-spacing: 0.5px; line-height: 1;
  }
  .card-back { left: 599px; background: var(--white); }
  .top-band { position: absolute; left: 0; top: 0; width: 100%; height: 32px; background: var(--green-light); }
  .top-notch { position: absolute; left: 0; top: 0; }
  .logo-block {
    position: absolute; left: 0; right: 0; top: 118px;
    display: flex; align-items: center; justify-content: center; gap: 12px;
  }
  .logo-mark { width: 30px; height: 30px; border-radius: 50%; background: var(--green-mid); }
  .back-brand { color: var(--ink); font-weight: 600; font-size: 54px; line-height: 1; }
  .name-band {
    position: absolute; left: 0; top: 332px; width: 100%; height: 98px;
    background: var(--green-mid); color: var(--white); text-align: center;
  }
  .person-name { font-weight: 600; font-size: 31px; line-height: 1; margin-top: 20px; }
  .person-title { font-weight: 500; font-size: 21px; line-height: 1; margin-top: 10px; }
  .contact-band {
    position: absolute; left: 0; top: 436px; width: 100%; height: 158px;
    background: var(--green-dark); color: var(--white); text-align: center;
    padding-top: 22px;
  }
  .contact-line { font-weight: 500; font-size: 21px; line-height: 1; margin-bottom: 11px; }
  .contact-email { font-size: 20px; }
</style>
</head>
<body>
<div class="canvas">
  <section class="card card-front" aria-label="Card front">
    <div class="front-brand">GreenVale</div>
  </section>

  <section class="card card-back" aria-label="Card back">
    <div class="top-band"></div>
    <svg class="top-notch" width="370" height="32" viewBox="0 0 370 32" aria-hidden="true">
      <polygon points="168,32 182,19 196,32" fill="#ffffff"/>
    </svg>
    <div class="logo-block">
      <span class="logo-mark"></span>
      <span class="back-brand">GreenVale</span>
    </div>
    <div class="name-band">
      <div class="person-name">DANIEL HARLOW JR.</div>
      <div class="person-title">PROJECT MANAGER</div>
    </div>
    <div class="contact-band">
      <div class="contact-line">555-204-0187 EXT.312</div>
      <div class="contact-line">555-630-4928</div>
      <div class="contact-line contact-email">DAN@GREENVALELANDSCAPES.COM</div>
    </div>
  </section>
</div>
</body>
</html>
```